Local massage therapist needs some new marketing material

Hi there! I am a massage therapist here in Denver, CO in Alder Bend(shopping and art district) of the city. My business is called Lumo Bodywork of Denver. My practice has an eastern influence and I do reflexology, thai massage and use Chinese herbs, etc. I know all my clients and pay close attention to details. I am also very respectful of tradition and it shows in how I work. I tend to like modern, clean, fun, Asian designs. I am wanting a new business card and brochure. I have a logo and branding for my business that I want used in the design. Currently, the sign for my building is purple and I think my logo was designed to be purple. I will attach pictures of it and can send whatever files are necessary so it can be integrated into the brochure, etc. I like the purple but open to using other colors as well. Thanks!
My website is lumobodyworkofdenver.example where info can be gathered about me and services/fees for brochure.
Updates

Just increased budget. Please see new feedback in discussion thread.

Thanks!

                                       HEY ALL,

Just wanted to let you know that I made a change to my website. It is on the Prices Page. I no longer have the frequent  flyer prices but I added discounts. Let me know if you have any questions. Thanks so much!

Target Market(s)

healthy, urban, educated, upper middle class, yogis

Industry/Entity Type

Marketing

Requirements
Must have
• logo stays purple
Should not have
• not too busy

```html
<!DOCTYPE html>
<html lang="en">
<head>
<meta charset="utf-8">
<title>Lumo Bodywork of Denver – Business Card</title>
<link rel="stylesheet" href="https://fonts.googleapis.com/css2?family=Open+Sans:ital,wght@0,400;0,600;0,700;1,400&display=swap">
<style>
  :root{
    --purple:#6a2ca0;
    --ink:#3f3f42;
    --muted:#6b6b70;
    --rule:#cfcfd4;
    --card:#ffffff;
    --backdrop:#e6e6ec;
  }
  *{box-sizing:border-box;margin:0;padding:0}
  html,body{width:1200px;height:987px;overflow:hidden}
  body{
    background:var(--backdrop);
    font-family:"Open Sans",Arial,sans-serif;
    color:var(--ink);
    display:flex;flex-direction:column;align-items:center;justify-content:center;gap:40px;
  }
  .card{
    width:760px;height:434px;background:var(--card);border-radius:28px;
    box-shadow:0 6px 18px rgba(40,30,60,.12);
    position:relative;overflow:hidden;
  }
  /* front */
  .brand{position:absolute;top:60px;left:0;right:0;display:flex;align-items:center;justify-content:center;gap:22px}
  .brand-dot{width:62px;height:62px;border:3px solid var(--purple);border-radius:50%}
  .brand-name{font-size:84px;font-weight:600;color:var(--purple);letter-spacing:10px;line-height:1}
  .divider{position:absolute;top:190px;left:60px;right:60px;height:2px;background:var(--rule)}
  .person{position:absolute;top:212px;left:0;right:0;text-align:center;font-size:30px;color:var(--purple);font-weight:700}
  .person .title{font-weight:400;color:var(--muted)}
  .contact{position:absolute;top:272px;left:0;right:0;text-align:center;font-size:21px;line-height:1.55}
  .contact .row{display:flex;justify-content:center;align-items:center;gap:8px}
  .icon{width:18px;height:18px;flex:none}
  .contact .web{gap:28px}
  .contact .web span{display:flex;align-items:center;gap:8px}
  /* back */
  .appt-title{position:absolute;top:36px;right:60px;font-size:24px;font-weight:700;color:var(--purple);letter-spacing:.5px}
  .field{position:absolute;left:60px;font-size:20px;color:var(--muted);display:flex;align-items:flex-end;gap:10px}
  .field .line{border-bottom:1px solid #9a9aa0;height:20px}
  .f-name{top:96px}.f-name .line{width:560px}
  .f-date{top:150px}.f-date .line{width:230px}
  .f-time .line{width:190px}
  .hours{position:absolute;top:232px;left:60px;right:60px;font-size:24px;line-height:1.4;color:var(--ink)}
  .cancel{position:absolute;top:330px;left:60px;font-size:21px;font-style:italic;color:var(--muted)}
</style>
</head>
<body>
  <section class="card card-front" aria-label="Card front">
    <div class="brand">
      <div class="brand-dot"></div>
      <div class="brand-name">LUMO</div>
    </div>
    <div class="divider"></div>
    <p class="person">Your Name, <span class="title">Title</span></p>
    <div class="contact">
      <p class="row">1485 E 9th Ave, Denver, CO 80218</p>
      <p class="row">
        <svg class="icon" viewBox="0 0 20 20"><circle cx="10" cy="10" r="9" fill="none" stroke="#3f3f42" stroke-width="1.6"/><path d="M6.5 5.5l2 .2.6 2.3-1.2.9a6 6 0 0 0 3.2 3.2l.9-1.2 2.3.6.2 2c-4.5.8-9-3.6-8-8z" fill="#3f3f42"/></svg>
        303.555.0148
      </p>
      <p class="row web">
        <span><svg class="icon" viewBox="0 0 20 20"><rect x="1.5" y="4" width="17" height="12" rx="1.5" fill="#3f3f42"/><path d="M2 5l8 6 8-6" fill="none" stroke="#fff" stroke-width="1.4"/></svg>info@lumobodyworkofdenver.example</span>
      </p>
      <p class="row">
        <svg class="icon" viewBox="0 0 20 20"><circle cx="10" cy="10" r="8.5" fill="none" stroke="#3f3f42" stroke-width="1.5"/><ellipse cx="10" cy="10" rx="3.8" ry="8.5" fill="none" stroke="#3f3f42" stroke-width="1.3"/><path d="M1.5 10h17M3 6h14M3 14h14" stroke="#3f3f42" stroke-width="1.2"/></svg>
        www.lumobodyworkofdenver.example
      </p>
    </div>
  </section>

  <section class="card card-back" aria-label="Card back">
    <h2 class="appt-title">YOUR APPOINTMENT</h2>
    <p class="field f-name">Name : <span class="line"></span></p>
    <p class="field f-date">Date : <span class="line"></span>
      <span class="f-time" style="display:flex;align-items:flex-end;gap:10px;margin-left:14px">Time : <span class="line"></span> am / pm</span>
    </p>
    <p class="hours">Tues - Fri 10am - 8pm Sat 10am-5pm<br>(Appointments required) No walk-ins please.</p>
    <p class="cancel">We appreciate a 24 hr. notice for cancellations</p>
  </section>
</body>
</html>
```